New Business Card Design Project

We require a business card design for Vexalund, a newly established Indian company.
Our focus is on the development, manufacturing, and export of a diverse array of pharmaceutical products on a global scale. The card should convey a professional appearance, as our primary markets are in Africa, China, and Southeast Asian nations.
We envision a two-sided business card, with the reverse side dedicated to a logo set against a solid color or an elegantly designed pattern. The corners should be rounded. We would appreciate seeing both horizontal and vertical design options. We trust the designer to utilize their expertise in creating this design.

The content for the business card is included in the attached Word file.

Target Market(s)

Our primary markets are in Africa, China, and Southeast Asian, Latin America, Maldives, Sri Lanka

Industry/Entity Type

Pharmaceutical Manufacturing and Export

Contact Information for Business Card

Colors

Designer to choose colors to be used in the design.

Requirements
Must have
• The reverse side of the business card features solely the logo along with the tagline, "Healing for All."
Should not have
• The logo should not exceed two instances, encompassing both the front and back sides of the card.

```html
<!DOCTYPE html>
<html lang="en">
<head>
<meta charset="utf-8">
<title>Vexalund Business Card</title>
<link href="https://fonts.googleapis.com/css2?family=Open+Sans:wght@300;400;600;700&display=swap" rel="stylesheet">
<style>
  :root {
    --stage: #232323;
    --card: #1f1f21;
    --blue: #27a6df;
    --red: #ef5a47;
    --ink: #e9e9ea;
    --shadow: rgba(0,0,0,0.55);
  }
  * { box-sizing: border-box; margin: 0; padding: 0; }
  html, body { width: 1200px; height: 780px; overflow: hidden; background: var(--stage); }
  body {
    font-family: "Open Sans", Arial, sans-serif;
    display: flex; align-items: center; justify-content: center; gap: 40px;
  }
  .card {
    position: relative; width: 540px; height: 310px;
    background: var(--card); border-radius: 22px; overflow: hidden;
    box-shadow: 0 18px 40px var(--shadow);
  }

  /* Front */
  .brand {
    position: absolute; left: 0; top: 0; width: 250px; height: 288px;
    display: flex; align-items: center; justify-content: center; gap: 10px;
  }
  .brand-dot { width: 16px; height: 16px; border-radius: 50%; background: var(--red); }
  .brand-name { font-weight: 700; font-size: 34px; color: var(--blue); letter-spacing: 0.5px; }
  .divider {
    position: absolute; left: 250px; bottom: 36px; width: 1.5px; height: 200px; background: var(--blue);
  }
  .details { position: absolute; left: 278px; top: 60px; right: 20px; color: var(--ink); }
  .person-name { font-size: 25px; font-weight: 600; color: var(--blue); line-height: 1.1; white-space: nowrap; }
  .person-name .surname { color: var(--red); font-weight: 400; }
  .person-role { font-size: 13px; margin-top: 2px; }
  .address { font-size: 12.5px; line-height: 1.45; margin-top: 14px; }
  .contacts { list-style: none; margin-top: 12px; font-size: 12.5px; line-height: 1.55; }
  .contacts li { display: flex; align-items: center; gap: 8px; white-space: nowrap; }
  .contacts svg { width: 13px; height: 13px; flex: none; }
  .band { position: absolute; left: 0; right: 0; bottom: 0; height: 22px; display: flex; }
  .band-red { width: 46%; background: var(--red); }
  .band-blue { flex: 1; background: var(--blue); }
  .band-marker {
    position: absolute; left: calc(46% - 13px); bottom: -2px; width: 26px; height: 26px;
    border-radius: 50%; background: var(--card); border: 4px solid var(--blue);
  }

  /* Back */
  .back { display: flex; flex-direction: column; align-items: center; justify-content: center; }
  .back .brand-row { display: flex; align-items: center; gap: 14px; }
  .back .brand-dot { width: 22px; height: 22px; }
  .back .brand-name { font-size: 52px; }
  .tagline { color: var(--ink); font-weight: 300; font-size: 14px; letter-spacing: 0.6px; margin-top: 10px; }
</style>
</head>
<body>

<section class="card front" aria-label="Card front">
  <div class="brand">
    <span class="brand-dot"></span>
    <span class="brand-name">Vexalund</span>
  </div>
  <div class="divider"></div>
  <div class="details">
    <p class="person-name">Arjun <span class="surname">K. Mehrota</span></p>
    <p class="person-role">CEO</p>
    <p class="address">12, Neelkamal Nagar,<br>Sarvadi, 441210, India</p>
    <ul class="contacts">
      <li>
        <svg viewBox="0 0 16 16" aria-hidden="true"><rect x="4" y="1" width="8" height="14" rx="1.5" fill="none" stroke="var(--red)" stroke-width="1.6"/></svg>
        +91 90001 23456
      </li>
      <li>
        <svg viewBox="0 0 16 16" aria-hidden="true"><circle cx="8" cy="8" r="6.5" fill="none" stroke="var(--blue)" stroke-width="1.6"/><path d="M1.5 8h13M8 1.5c-3 3-3 10 0 13M8 1.5c3 3 3 10 0 13" fill="none" stroke="var(--blue)" stroke-width="1.2"/></svg>
        www.vexalund.com
      </li>
      <li>
        <svg viewBox="0 0 16 16" aria-hidden="true"><rect x="1" y="3" width="14" height="10" rx="1" fill="var(--red)"/><path d="M1.5 3.5 8 9l6.5-5.5" fill="none" stroke="var(--card)" stroke-width="1.4"/></svg>
        amehrota@vexalund.com
      </li>
    </ul>
  </div>
  <div class="band">
    <div class="band-red"></div>
    <div class="band-blue"></div>
  </div>
  <div class="band-marker"></div>
</section>

<section class="card back" aria-label="Card back">
  <div class="brand-row">
    <span class="brand-dot"></span>
    <span class="brand-name">Vexalund</span>
  </div>
  <p class="tagline">Healing for All.</p>
</section>

</body>
</html>
```